Willow Creek Gatherings Event Planning in need of a design!!

Event Planning company, does a variety of events. I like simple more rustic designs focused on almond blossoms. We are based out of Northern California, the heart of almond country. I would like to see colors in light pinks, beige, light browns, whites or creams. the final design should communicate rustic simplicity. Below are some pictures of Almond blossoms and design ideas I prefer the one called Tulip Grove. Thanks

Target Market(s)

Women in the mid twenties and older. They should be in the upper middle class in need of an amazing party design and coordinator

Industry/Entity Type

Event Planning

Contact Information for Business Card

Maren Lockwood 530-624-0295almondbaffairs@gmail.comalmondblossomaffairs.com

Font styles to use
Other font styles liked:
• Amatic SC

Requirements
Must have
• almond blossom
• my information
• simplicity
Nice to have
• rustic design
• vintage feel
• whimsical
Should not have
• i like pink but not over the top

```html
<!DOCTYPE html>
<html lang="en">
<head>
<meta charset="utf-8">
<title>Willow Creek Gatherings – Business Card</title>
<link href="https://fonts.googleapis.com/css2?family=Yellowtail&family=Arimo:wght@400&display=swap" rel="stylesheet">
<style>
  :root {
    --page-bg: #efece7;
    --mint: #b5dfc3;
    --white: #ffffff;
    --orchard-sky: #c9d7de;
    --orchard-bloom: #d9d2cc;
    --orchard-grass: #6f9a4a;
    --blossom-white: #eeeae6;
    --blossom-green: #9aa98a;
    --blossom-brown: #7d6a5c;
    --card-shadow: rgba(60, 45, 30, 0.18);
  }
  * { box-sizing: border-box; margin: 0; padding: 0; }
  html, body {
    width: 1200px; height: 676px; overflow: hidden;
    background: var(--page-bg);
  }
  .stage {
    position: relative; width: 1200px; height: 676px;
  }
  .card {
    position: absolute; top: 190px;
    width: 520px; height: 297px;
    overflow: hidden;
    box-shadow: 0 8px 24px var(--card-shadow);
    background: var(--white);
  }
  .card--front { left: 60px; }
  .card--back { left: 620px; }
  .card__art { position: absolute; inset: 0; width: 100%; height: 100%; }

  .front__details {
    position: absolute; left: 250px; top: 22px; width: 250px;
    display: flex; flex-direction: column; align-items: center;
    color: var(--white); text-align: center;
  }
  .front__mark {
    width: 78px; height: 78px; border-radius: 50%;
    border: 3px solid var(--white);
  }
  .script-name {
    font-family: "Yellowtail", cursive;
    font-weight: 400; color: var(--white);
  }
  .front__script { font-size: 40px; line-height: 1; margin-top: 6px; }
  .front__caps {
    font-family: "Arimo", sans-serif; font-size: 18px;
    letter-spacing: 1px; text-transform: uppercase; margin-top: 14px;
  }
  .front__contact {
    font-family: "Arimo", sans-serif; font-size: 15px; line-height: 1.3;
    margin-top: 12px;
  }

  .back__name {
    position: absolute; left: 28px; top: 118px;
    font-size: 54px; line-height: 1;
    text-shadow: 0 1px 3px rgba(0,0,0,0.35);
  }
  .back__web {
    position: absolute; left: 150px; top: 188px;
    font-family: "Arimo", sans-serif; font-size: 15px; color: var(--white);
    text-shadow: 0 1px 2px rgba(0,0,0,0.35);
  }
</style>
</head>
<body>
<main class="stage">

  <section class="card card--front" aria-label="Business card front">
    <svg class="card__art" viewBox="0 0 520 297" preserveAspectRatio="none">
      <defs>
        <linearGradient id="orchard" x1="0" y1="0" x2="0" y2="1">
          <stop offset="0" stop-color="var(--orchard-sky)"/>
          <stop offset="0.45" stop-color="var(--orchard-bloom)"/>
          <stop offset="0.75" stop-color="var(--orchard-grass)"/>
          <stop offset="1" stop-color="var(--orchard-bloom)"/>
        </linearGradient>
      </defs>
      <rect class="front__mint" width="520" height="297" fill="var(--mint)"/>
      <path class="front__curve-band" d="M0 0 H250 C215 80 195 150 110 200 C70 225 30 250 0 262 Z" fill="var(--white)"/>
      <path class="front__photo" role="img" aria-label="Photo of a blossoming almond orchard row"
            d="M0 0 H236 C202 78 182 140 100 188 C62 210 28 232 0 244 Z" fill="url(#orchard)"/>
    </svg>
    <div class="front__details">
      <div class="front__mark" aria-hidden="true"></div>
      <p class="script-name front__script">Maren Lockwood</p>
      <p class="front__caps">Maren Lockwood</p>
      <p class="front__contact">530-817-4362<br>willowcgather@mailbox.test</p>
    </div>
  </section>

  <section class="card card--back" aria-label="Business card back">
    <svg class="card__art" viewBox="0 0 520 297" preserveAspectRatio="none">
      <defs>
        <radialGradient id="blossom" cx="0.7" cy="0.35" r="0.8">
          <stop offset="0" stop-color="var(--blossom-white)"/>
          <stop offset="0.45" stop-color="#c9c7bd"/>
          <stop offset="0.8" stop-color="var(--blossom-green)"/>
          <stop offset="1" stop-color="var(--blossom-brown)"/>
        </radialGradient>
      </defs>
      <rect class="back__photo" role="img" aria-label="Close-up photo of white almond blossoms on a branch"
            width="520" height="297" fill="url(#blossom)"/>
    </svg>
    <p class="script-name back__name">Maren Lockwood</p>
    <p class="back__web">willowcreekgatherings.test</p>
  </section>

</main>
</body>
</html>
```